Business card design for Automotive workshop

We need a business card for a new automotive repair and tyre shop called Keelstone Prime Automotive located in New Zealand. We are a clean, modern and fresh workshop and company.

Front needs to feature logo,
my name:
Marlo Fenwicke (director)

Address:
48 Tarn Lane
Korimako Bay 3592

Phone: 07 594 2713
Mobile: 027 451 9362
Email: office@keelstoneautomotive.example.nz
Website: keelstoneautomotive.example.nz

Back needs to feature an area to write down appointment details, date and time.

Also feature a list of jobs and work we do such as,
Vehicle Servicing
All Mechanical Repairs
Warrant of Fitness
Tyres & Wheel Alignments
Automotive Diagnostics
Automotive Parts & Supplies

```html
<!DOCTYPE html>
<html lang="en">
<head>
<meta charset="utf-8">
<title>Keelstone Prime Automotive – Business Card</title>
<link rel="stylesheet" href="https://fonts.googleapis.com/css2?family=Exo+2:wght@400;500;600;700&display=swap">
<style>
  :root {
    --bg: #2b2d30;
    --card-black: #0c0c0d;
    --card-white: #ffffff;
    --red: #e0202a;
    --text-light: #f2f2f2;
    --text-dark: #1a1a1a;
    --dash: #6b6b6b;
  }
  * { box-sizing: border-box; margin: 0; padding: 0; }
  html, body { width: 1200px; height: 900px; overflow: hidden; }
  body {
    background: var(--bg);
    font-family: "Exo 2", sans-serif;
    position: relative;
  }
  .card {
    position: absolute;
    left: 270px;
    width: 660px;
    height: 377px;
    overflow: hidden;
    box-shadow: 0 10px 30px rgba(0,0,0,.45);
  }
  .card--back { top: 52px; background: var(--card-white); }
  .card--front { top: 471px; background: var(--card-black); color: var(--text-light); }

  /* Back */
  .back-shapes { position: absolute; inset: 0; }
  .brand {
    position: absolute;
    display: flex;
    align-items: center;
    gap: 10px;
    font-weight: 700;
    text-transform: uppercase;
    letter-spacing: 1.5px;
    color: var(--text-light);
  }
  .brand__square { width: 14px; height: 14px; background: var(--red); flex: none; }
  .card--back .brand { right: 34px; top: 44px; font-size: 25px; }
  .services { position: absolute; top: 136px; list-style: none; font-size: 14px; font-weight: 500; text-transform: uppercase; color: var(--text-dark); letter-spacing: .5px; line-height: 22px; }
  .services--left { left: 34px; }
  .services--right { right: 34px; text-align: right; }
  .services li { display: flex; align-items: center; gap: 8px; }
  .services--right li { justify-content: flex-end; }
  .services--left li::before, .services--right li::after {
    content: ""; width: 8px; height: 8px; border-radius: 50%; background: var(--red); flex: none;
  }
  .appointment { position: absolute; left: 34px; right: 34px; top: 222px; }
  .appointment__line { border-bottom: 1.5px dashed var(--dash); height: 34px; }
  .appointment__row { display: flex; gap: 24px; }
  .appointment__field { flex: 1; display: flex; align-items: flex-end; gap: 8px; height: 40px; font-size: 14px; font-weight: 500; color: var(--text-dark); }
  .appointment__field span { flex: 1; border-bottom: 1.5px dashed var(--dash); height: 1px; margin-bottom: 3px; }

  /* Front */
  .card--front .brand { left: 38px; top: 110px; font-size: 24px; flex-direction: column; align-items: flex-start; gap: 4px; line-height: 1.1; }
  .brand__row { display: flex; align-items: center; gap: 10px; }
  .divider { position: absolute; left: 320px; top: 90px; width: 1.5px; height: 150px; background: var(--red); }
  .contact { position: absolute; left: 342px; top: 92px; }
  .contact__name { font-size: 24px; font-weight: 700; text-transform: uppercase; color: var(--red); letter-spacing: 1.5px; }
  .contact__role { font-size: 15px; margin: 2px 0 12px; }
  .contact__list { list-style: none; font-size: 14px; line-height: 23px; }
  .contact__list li { display: flex; align-items: center; gap: 9px; }
  .contact__list svg { width: 13px; height: 13px; flex: none; }
  .address { position: absolute; left: 38px; bottom: 40px; font-size: 15px; }
</style>
</head>
<body>

<section class="card card--back" aria-label="Card back – appointment">
  <svg class="back-shapes" viewBox="0 0 660 377" width="660" height="377" aria-hidden="true">
    <polygon points="0,0 182,0 142,40 0,40" fill="#e0202a"/>
    <polygon points="206,0 660,0 660,118 88,118" fill="#0c0c0d"/>
  </svg>
  <div class="brand"><span class="brand__square"></span>Keelstone Prime Automotive</div>
  <ul class="services services--left">
    <li>Vehicle Servicing</li>
    <li>All Mechanical Repairs</li>
    <li>Warrant of Fitness</li>
  </ul>
  <ul class="services services--right">
    <li>Tyres &amp; Wheel Alignments</li>
    <li>Automotive Diagnostics</li>
    <li>Automotive Parts &amp; Supplies</li>
  </ul>
  <div class="appointment">
    <div class="appointment__line"></div>
    <div class="appointment__line"></div>
    <div class="appointment__row">
      <div class="appointment__field">DATE:<span></span></div>
      <div class="appointment__field">TIME:<span></span></div>
    </div>
  </div>
</section>

<section class="card card--front" aria-label="Card front – contact">
  <div class="brand">
    <div class="brand__row"><span class="brand__square"></span>Keelstone</div>
    <div>Prime Automotive</div>
  </div>
  <div class="divider"></div>
  <div class="contact">
    <p class="contact__name">Marlo Fenwicke</p>
    <p class="contact__role">Director</p>
    <ul class="contact__list">
      <li><svg viewBox="0 0 16 16" aria-hidden="true"><circle cx="8" cy="8" r="7" fill="none" stroke="#e0202a" stroke-width="1.4"/><path d="M5.5 4.5l1.5 1.5-.8 1c.6 1.1 1.4 1.9 2.5 2.5l1-.8 1.5 1.5-1 1c-2.6-.4-4.8-2.6-5.2-5.2z" fill="#e0202a"/></svg>07 594 2713</li>
      <li><svg viewBox="0 0 16 16" aria-hidden="true"><rect x="4" y="1" width="8" height="14" rx="1.5" fill="none" stroke="#e0202a" stroke-width="1.4"/><circle cx="8" cy="12.5" r=".9" fill="#e0202a"/></svg>027 451 9362</li>
      <li><svg viewBox="0 0 16 16" aria-hidden="true"><rect x="1.5" y="3.5" width="13" height="9" fill="none" stroke="#e0202a" stroke-width="1.4"/><path d="M1.5 3.5L8 9l6.5-5.5" fill="none" stroke="#e0202a" stroke-width="1.4"/></svg>office@keelstoneautomotive.example.nz</li>
      <li><svg viewBox="0 0 16 16" aria-hidden="true"><circle cx="8" cy="8" r="6.5" fill="none" stroke="#e0202a" stroke-width="1.4"/><ellipse cx="8" cy="8" rx="2.8" ry="6.5" fill="none" stroke="#e0202a" stroke-width="1.2"/><path d="M1.5 8h13" stroke="#e0202a" stroke-width="1.2"/></svg>keelstoneautomotive.example.nz</li>
    </ul>
  </div>
  <p class="address">48 Tarn Lane, Korimako Bay 3592</p>
</section>

</body>
</html>
```